Business Card Design

Company is a Commercial Building Company specialising in New Construction and existing refurbishments

Industry/Entity Type

Business

Contact Information for Business Card

Liam Porter
Construction Manager
E Liam@marshbuilding.com.au
M 0400 213 594
Mail 14 Tarrant Rise Kestrel Bay WA 6274

```html
<!DOCTYPE html>
<html lang="en">
<head>
<meta charset="utf-8">
<title>Marsh Building &amp; Construction – Business Card</title>
<link rel="stylesheet" href="https://fonts.googleapis.com/css2?family=Roboto:ital,wght@0,400;0,500;0,700;1,400&display=swap">
<style>
  :root {
    --backdrop: #e9e6e1;
    --card: #f7f7f6;
    --navy: #3e4759;
    --teal: #1fa9c9;
    --orange: #e8781c;
    --white: #ffffff;
  }
  * { margin: 0; padding: 0; box-sizing: border-box; }
  html, body { width: 1200px; height: 804px; overflow: hidden; }
  body {
    background: var(--backdrop);
    font-family: "Roboto", Arial, sans-serif;
    position: relative;
  }
  .card {
    position: absolute;
    top: 257px;
    width: 478px;
    height: 290px;
    background: var(--card);
    box-shadow: 0 2px 6px rgba(0,0,0,.18);
    overflow: hidden;
  }
  .card--front { left: 108px; }
  .card--back { left: 613px; }

  /* Front */
  .front-brand {
    position: absolute;
    left: 0; right: 0; top: 62px;
    text-align: center;
  }
  .brand-square {
    display: block;
    width: 84px; height: 84px;
    margin: 0 auto 26px;
    background: var(--teal);
  }
  .brand-name {
    color: var(--navy);
    font-weight: 500;
    text-transform: uppercase;
    line-height: 1.15;
  }
  .front-brand .brand-name { font-size: 22px; }
  .front-stripes { position: absolute; left: 0; bottom: 0; }

  /* Back */
  .back-brand {
    position: absolute;
    left: 30px; top: 34px;
    display: flex; align-items: center; gap: 14px;
  }
  .back-brand .brand-square { width: 50px; height: 50px; margin: 0; }
  .back-brand .brand-name { font-size: 23px; }
  .holder { position: absolute; left: 30px; top: 134px; }
  .holder-name {
    color: var(--navy);
    font-size: 21px; font-weight: 700;
    letter-spacing: 1.5px; text-transform: uppercase;
  }
  .holder-role {
    color: var(--teal);
    font-size: 14px; font-style: italic; margin-top: 3px;
  }
  .back-waves { position: absolute; left: 0; top: 0; }
  .contacts {
    position: absolute; right: 20px; top: 196px;
    list-style: none; color: var(--white);
    font-size: 11.5px;
  }
  .contacts li {
    display: flex; justify-content: flex-end; align-items: center;
    gap: 7px; height: 18.5px;
  }
  .contacts svg { width: 11px; height: 11px; flex: none; }
</style>
</head>
<body>

<section class="card card--front" aria-label="Card front">
  <div class="front-brand">
    <span class="brand-square" aria-hidden="true"></span>
    <p class="brand-name">Marsh Building<br>&amp; Construction</p>
  </div>
  <svg class="front-stripes" width="478" height="12" viewBox="0 0 478 12" aria-hidden="true">
    <polygon points="0,2 348,2 342,12 0,12" fill="var(--teal)"/>
    <polygon points="350,2 478,2 478,12 344,12" fill="var(--orange)"/>
  </svg>
</section>

<section class="card card--back" aria-label="Card back">
  <div class="back-brand">
    <span class="brand-square" aria-hidden="true"></span>
    <p class="brand-name">Marsh Building<br>&amp; Construction</p>
  </div>

  <div class="holder">
    <p class="holder-name">Liam Porter</p>
    <p class="holder-role">Construction Manager</p>
  </div>

  <svg class="back-waves" width="478" height="290" viewBox="0 0 478 290" aria-hidden="true">
    <path d="M0,206 C90,250 190,252 272,228 C190,266 80,262 0,238 Z" fill="var(--teal)"/>
    <path d="M0,250 C100,292 200,272 292,216 C370,165 420,122 478,118 L478,290 L0,290 Z" fill="var(--navy)"/>
    <path d="M45,234 C150,256 230,238 300,190 C370,142 420,112 478,104 L478,114 C420,122 372,158 302,204 C232,250 150,262 45,234 Z" fill="var(--orange)"/>
  </svg>

  <ul class="contacts">
    <li>0400 213 594
      <svg viewBox="0 0 12 12" aria-hidden="true"><rect x="3" y="0.5" width="6" height="11" rx="1" fill="none" stroke="var(--teal)" stroke-width="1.2"/><circle cx="6" cy="9.6" r=".7" fill="var(--teal)"/></svg>
    </li>
    <li>Liam@marshbuilding.com.au
      <svg viewBox="0 0 12 12" aria-hidden="true"><rect x="0.5" y="2.5" width="11" height="7" fill="var(--teal)"/><path d="M0.5,2.5 L6,6.5 L11.5,2.5" fill="none" stroke="var(--navy)" stroke-width="1"/></svg>
    </li>
    <li>www.marshbuilding.com.au
      <svg viewBox="0 0 12 12" aria-hidden="true"><circle cx="6" cy="6" r="5" fill="var(--teal)"/><path d="M1,6 H11 M6,1 C3,4 3,8 6,11 M6,1 C9,4 9,8 6,11" fill="none" stroke="var(--navy)" stroke-width=".8"/></svg>
    </li>
    <li>14 Tarrant Rise Kestrel Bay WA 6274
      <svg viewBox="0 0 12 12" aria-hidden="true"><path d="M6,11.5 C3,7.5 2,6 2,4.3 A4,4 0 0 1 10,4.3 C10,6 9,7.5 6,11.5 Z" fill="var(--teal)"/><circle cx="6" cy="4.3" r="1.5" fill="var(--navy)"/></svg>
    </li>
  </ul>
</section>

</body>
</html>
```